Agriculture farming Hemp and CBD

The logo is in works with your company now, should be ready in a few days. We have our Domain (kestrelbrookhollow.com) We would like to see incorporated seed to growth, but not necessary. we would like to nature colors and some black and green. we have our farm and will be growing and selling HEMP and CBD we are based in the state of Virginia. Would like to incorporate the words pause, play, rewind if possible but not necessary.

Target Market(s)

20 years old to elderly

Coding

Coded - Design and coding required

Number of Pages Required

3 page

Font styles to use
Serif

Requirements
Must have
• I'm not sure on the must haves, we are open to any ideas, we would definitely like to see Hemp and CBD included, may the life cycle of seed to plant. We must have a pop up asking if you are 20 years old before they can enter our site and to view or purchase our product. I want the design to be totally different than what i uploaded.
Nice to have
• Would like to see natural colors as well as black and green
Should not have
• I want

```html
<!DOCTYPE html>
<html lang="en">
<head>
<meta charset="utf-8">
<title>Kestrel Brook Hollow — Home</title>
<link href="https://fonts.googleapis.com/css2?family=Libre+Baskerville:ital,wght@0,400;0,700;1,400&family=Open+Sans:ital,wght@0,400;0,600;0,700;1,400&display=swap" rel="stylesheet">
<style>
:root{
  --board:#149626;
  --green:#1a9a2a;
  --green-light:#2fbb35;
  --yellow:#e5c21a;
  --ink:#222;
  --muted:#666;
  --dark:#0f1411;
  --footer:#16201c;
  --paper:#fff;
  --mist:#eeeeee;
  --serif:'Libre Baskerville',Georgia,serif;
  --sans:'Open Sans',Arial,sans-serif;
}
*{box-sizing:border-box;margin:0;padding:0}
html,body{width:851px;height:1200px;overflow:hidden}
body{background:var(--board);position:relative;font-family:var(--sans);color:var(--ink)}
.page{position:absolute;top:21px;width:397px;height:1136px;background:var(--paper);overflow:hidden}
.page--gate{left:22.5px}
.page--open{left:431px}
.abs{position:absolute}

/* hero */
.hero{position:absolute;left:0;top:0;width:397px;height:184px;background:radial-gradient(ellipse at 75% 30%,#2c3f2a 0%,#172417 45%,#0b0f0b 100%)}
.brand{position:absolute;font-family:var(--sans);font-weight:600;color:#fff;white-space:nowrap}
.hero .brand{left:38px;top:10px;font-size:6.5px}
.nav{position:absolute;top:10px;left:0;font-size:5.5px;color:#fff}
.nav span{position:absolute;white-space:nowrap}
.nav .active{color:var(--green-light)}
.nav .active::after{content:"";position:absolute;left:0;right:0;top:10px;height:1px;background:var(--green-light)}
.search{position:absolute;left:353px;top:11px}
.hero-title{position:absolute;left:36px;top:48px;font-family:var(--serif);font-size:18.5px;color:#fff;white-space:nowrap}
.hero-text{position:absolute;left:36px;top:78px;font-size:5.6px;line-height:10.6px;color:#e8e8e8}
.btn{position:absolute;background:var(--green);color:#fff;font-size:5.3px;font-weight:700;text-align:center;border-radius:2px;letter-spacing:.2px}
.hero .btn{left:36px;top:120px;width:50px;height:17px;line-height:17px}
.rail{position:absolute;left:357px;width:1px;background:#bbb}
.notch{position:absolute;left:0;bottom:-1px}

/* history */
.history{position:absolute;left:0;top:184px;width:397px;height:191px;background:var(--paper)}
.history-photo{position:absolute;left:8px;top:24px;width:178px;height:151px;background:radial-gradient(ellipse at 45% 55%,#9fb36c 0%,#c9d0b5 30%,#f2f2f0 65%,#f7f7f7 100%)}
.eyebrow{position:absolute;font-size:5.6px;letter-spacing:2.6px;color:var(--green-light);white-space:nowrap}
.heading{position:absolute;font-family:var(--serif);font-size:9.4px;color:var(--ink);white-space:nowrap}
.center{left:0;width:397px;text-align:center}
.history .eyebrow{left:198px;top:33px}
.history .heading{left:198px;top:46px}
.history-text{position:absolute;left:198px;top:68px;width:161px;font-size:5.1px;line-height:8.5px;color:var(--muted);text-align:justify}
.history .btn{left:198px;top:137px;width:50px;height:18px;line-height:18px}

/* services */
.services{position:absolute;left:0;top:375px;width:397px;height:154px;background:linear-gradient(180deg,#26321f 0%,#1f2a1b 50%,#141a12 100%)}
.services .eyebrow{top:31px;color:#e6e6e6}
.services .heading{top:44px;color:#fff}
.service{position:absolute;top:64px;width:80px;text-align:center;color:#fff}
.service svg{display:block;margin:0 auto}
.service h3{font-family:var(--serif);font-weight:400;font-size:6.3px;margin-top:5px;letter-spacing:.2px}
.service p{font-size:4.8px;line-height:8.4px;color:#ddd;margin-top:2px}

/* clients */
.clients{position:absolute;left:0;top:529px;width:397px;height:182px;background:var(--paper)}
.clients .eyebrow{top:29px}
.clients .heading{top:43px}
.quote{position:absolute;top:70px;width:102px;height:68px;border:0.6px solid #bdbdbd;font-style:italic;font-size:4.5px;line-height:8.4px;color:#777;text-align:center;padding-top:9px}
.avatar{position:absolute;left:40px;top:57px;width:22px;height:22px;background:linear-gradient(180deg,#6b6b6b,#3c3c3c);border:0.6px solid #999}
.client-name{position:absolute;left:0;top:85px;width:100%;font-family:var(--serif);font-style:normal;font-size:6.4px;color:#444;line-height:8px}

/* blog */
.blog{position:absolute;left:0;top:711px;width:397px;height:240px;background:var(--mist)}
.blog .eyebrow{top:42px}
.blog .heading{top:55px}
.post{position:absolute;width:159px;height:58px;background:#fff;box-shadow:0 0 2px rgba(0,0,0,.15)}
.post-photo{position:absolute;left:0;top:0;width:76px;height:58px}
.post-body{position:absolute;left:76px;top:0;width:83px;height:58px;padding:4px 0 0 5px}
.post-title{font-family:var(--serif);font-size:5.4px;line-height:8.6px;color:#b6891e;position:relative}
.post-date{position:absolute;right:6px;top:8.6px;font-family:var(--sans);font-size:3.8px;font-weight:700;color:#333}
.post-text{font-size:4.6px;line-height:8.5px;color:#777;margin-top:1px}
.post--active .post-body{background:var(--green)}
.post--active .post-title,.post--active .post-text,.post--active .post-date{color:#fff}

/* footer */
.footer{position:absolute;left:0;top:951px;width:397px;height:185px;background:linear-gradient(180deg,#1a2420 0%,#18221d 60%,#121a16 100%);color:#fff}
.news-label{position:absolute;left:41px;top:19px;font-family:var(--serif);font-size:6.3px;white-space:nowrap}
.news-input{position:absolute;left:177px;top:14px;width:94px;height:18px;border:0.6px solid #9aa;font-size:4px;color:#ccc;padding:7px 0 0 3px}
.news-btn{position:absolute;left:280px;top:17px;width:42px;height:14px;line-height:14px;background:#1f5a2e;font-size:4.6px;font-weight:700;text-align:center}
.rule{position:absolute;left:37px;top:41px;width:323px;height:0.6px;background:#56645d}
.footer .brand{left:41px;top:68px;font-size:9px}
.footer-about{position:absolute;left:37px;top:90px;width:97px;font-size:5px;line-height:8.5px;color:#ddd;text-align:justify}
.socials{position:absolute;left:64px;top:131px}
.socials i{display:inline-block;width:4.5px;height:4.5px;background:#ddd;margin-right:6px;border-radius:.6px}
.col-title{position:absolute;font-family:var(--serif);font-size:6.3px;white-space:nowrap}
.links{position:absolute;left:180px;top:83px;font-size:5px;line-height:8.5px;color:#ddd}
.contact-row{position:absolute;left:277px;font-size:5px;line-height:8.4px;color:#ddd;white-space:nowrap}
.contact-row svg{position:absolute;left:0;top:1px}
.contact-row span{display:block;padding-left:9px}
.copyright{position:absolute;left:0;width:397px;top:150px;text-align:center;font-size:3.9px;color:#ccc}
.code{position:absolute;left:380px;top:150px;font-size:3.9px;color:#ccc}

/* age gate */
.gate-shade{position:absolute;inset:0;background:rgba(40,40,40,.45)}
.gate{position:absolute;left:84px;top:56px;width:228px;height:127px;background:#fff}
.gate-question{position:absolute;left:0;top:38px;width:228px;text-align:center;font-family:var(--serif);font-size:12px;color:#222}
.gate-btn{position:absolute;top:69px;width:55px;height:19px;line-height:19px;text-align:center;font-family:var(--serif);font-size:6px;color:#fff;border-radius:1.5px}
.gate-yes{left:47px;background:var(--green)}
.gate-no{left:126px;background:var(--yellow)}
</style>
</head>
<body>

<!-- ============ PAGE WITH AGE GATE ============ -->
<div class="page page--gate">
  <section class="hero" role="img" aria-label="Dark close-up of hemp leaves">
    <div class="brand">kestrelbrookhollow.com</div>
    <nav class="nav"><span class="active" style="left:153px">Home</span><span style="left:184px">About Us</span><span style="left:224px">Services</span><span style="left:261px">Blog</span><span style="left:289px">Contact Us</span></nav>
    <svg class="search" width="6" height="6" viewBox="0 0 6 6"><circle cx="2.4" cy="2.4" r="1.8" fill="none" stroke="#fff" stroke-width=".8"/><line x1="3.7" y1="3.7" x2="5.5" y2="5.5" stroke="#fff" stroke-width=".8"/></svg>
    <h1 class="hero-title">Pause, Play, Rewind</h1>
    <p class="hero-text">Lorem ipsum dolor sit amet, consectetur adipiscing elit, sed<br>do eiusmod tempor incididunt ut labore et dolore magna<br>aliqua.</p>
    <div class="btn">GET STARTED</div>
    <div class="rail" style="top:65px;height:11px;width:1.2px;background:#fff"></div>
    <div class="rail" style="top:81px;height:21px"></div>
    <div class="rail" style="top:105px;height:14px"></div>
    <svg class="notch" width="397" height="13" viewBox="0 0 397 13"><path d="M168 13 C180 13 182 1 199 1 C216 1 218 13 230 13 Z" fill="#fff"/><rect x="197" y="4" width="4" height="6" rx="2" fill="none" stroke="#555" stroke-width=".5"/></svg>
  </section>

  <section class="history">
    <div class="history-photo" role="img" aria-label="Hemp seedlings sprouting from soil-filled shells with green leaves"></div>
    <div class="eyebrow">LOREM IPSUM DOLOR SIT</div>
    <h2 class="heading">HISTORY ABOUT KESTREL BROOK</h2>
    <p class="history-text">Lorem ipsum dolor sit amet, consectetur adipiscing elit, sed do eiusmod tempor incididunt ut labore et dolore magna aliqua. Ut enim ad minim veniam, quis nostrud exercitation ullamco laboris nisi ut aliquip ex ea commodo consequat. Duis aute irure dolor in reprehenderit in voluptate velit esse cillum dolore eu fugiat nulla pariatur. Excepteur sint occaecat cupidatat non proident, sunt in culpa qui officia deserunt mollit anim id est laborum.</p>
    <div class="btn">GET STARTED</div>
  </section>

  <section class="services" role="img" aria-label="Dark field of hemp plants behind the services list">
    <div class="eyebrow center">LOREM IPSUM DOLOR SIT</div>
    <h2 class="heading center">OUR SERVICES</h2>
    <div class="service" style="left:34px"><svg width="16" height="16" viewBox="0 0 16 16" fill="none" stroke="#d9a420" stroke-width=".9"><path d="M2 14 C6 12 10 4 14 2"/><path d="M2 10 C6 12 10 4 14 6"/><line x1="5" y1="9" x2="7" y2="11"/><line x1="8" y1="6" x2="10" y2="8"/></svg><h3>GENETICS</h3><p>Lorem ipsum dolor sit amet,<br>consectetur adipiscing elit, sed<br>do eiusmod tempor.</p></div>
    <div class="service" style="left:117px"><svg width="16" height="16" viewBox="0 0 16 16" fill="none" stroke="#d9a420" stroke-width=".9"><rect x="5" y="1" width="10" height="8"/><line x1="7" y1="4" x2="13" y2="4"/><line x1="7" y1="6" x2="11" y2="6"/><circle cx="4" cy="10" r="2"/><path d="M1 15 C1 12 7 12 7 15"/></svg><h3>CONSULTING</h3><p>Lorem ipsum dolor sit amet,<br>consectetur adipiscing elit, sed<br>do eiusmod tempor.</p></div>
    <div class="service" style="left:200px"><svg width="16" height="16" viewBox="0 0 16 16" fill="#d9a420"><circle cx="8" cy="7" r="2"/><circle cx="3" cy="4" r="1"/><circle cx="13" cy="3" r="1"/><circle cx="14" cy="9" r="1"/><circle cx="10" cy="1.5" r=".8"/><rect x="7.5" y="9" width="1" height="6"/></svg><h3>ANCILLARY</h3><p>Lorem ipsum dolor sit amet,<br>consectetur adipiscing elit, sed<br>do eiusmod tempor.</p></div>
    <div class="service" style="left:281px"><svg width="16" height="16" viewBox="0 0 16 16" fill="none" stroke="#d9a420" stroke-width=".9"><rect x="3" y="1" width="10" height="14" rx="1"/><circle cx="7" cy="6" r="2"/><line x1="10" y1="5" x2="12" y2="5"/><line x1="5" y1="11" x2="5" y2="13"/><line x1="8" y1="10" x2="8" y2="13"/><line x1="11" y1="9" x2="11" y2="13"/></svg><h3>BIOMASS PROGRAM</h3><p>Lorem ipsum dolor sit amet,<br>consectetur adipiscing elit, sed<br>do eiusmod tempor.</p></div>
  </section>

  <section class="clients">
    <div class="eyebrow center">LOREM IPSUM DOLOR SIT</div>
    <h2 class="heading center">WHAT OUR CLIENTS SAY</h2>
    <div class="quote" style="left:37px">Lorem ipsum dolor sit amet, conse<br>ctetur adipiscing elit, sed do eiusmod tempor<br>incididunt ut labore et dolore magna aliqua.<br>Ut enim ad minim veniam, quis nostrud<br>exercitation ullamco laboris nisi ut<div class="avatar" role="img" aria-label="Client portrait"></div><div class="client-name">John Doe</div></div>
    <div class="quote" style="left:147px">Lorem ipsum dolor sit amet, conse<br>ctetur adipiscing elit, sed do eiusmod tempor<br>incididunt ut labore et dolore magna aliqua.<br>Ut enim ad minim veniam, quis nostrud<br>exercitation ullamco laboris nisi ut<div class="avatar" role="img" aria-label="Client portrait"></div><div class="client-name">John Doe</div></div>
    <div class="quote" style="left:258px">Lorem ipsum dolor sit amet, conse<br>ctetur adipiscing elit, sed do eiusmod tempor<br>incididunt ut labore et dolore magna aliqua.<br>Ut enim ad minim veniam, quis nostrud<br>exercitation ullamco laboris nisi ut<div class="avatar" role="img" aria-label="Client portrait"></div><div class="client-name">John Doe</div></div>
  </section>

  <section class="blog">
    <div class="eyebrow center">LOREM IPSUM DOLOR SIT</div>
    <h2 class="heading center">OUR LATEST BLOG</h2>
    <article class="post" style="left:37px;top:80px"><div class="post-photo" role="img" aria-label="Hemp plant in sunlight" style="background:linear-gradient(135deg,#e9e2a8,#6f8a3a 45%,#2f4a1e)"></div><div class="post-body"><div class="post-title">CONSECTETUR ADIPIS<br>CING ELIT<span class="post-date">02-SEP-2020</span></div><p class="post-text">sed do eiusmod tempor incidi<br>dunt ut labore et dolore magna<br>aliqua. Ut enim ad minim veni<br>am, quis nostrud</p></div></article>
    <article class="post" style="left:201px;top:80px"><div class="post-photo" role="img" aria-label="Researcher inspecting hemp plants" style="background:linear-gradient(135deg,#c9cfc2,#7c8f62 50%,#3d5128)"></div><div class="post-body"><div class="post-title">CONSECTETUR ADIPIS<br>CING ELIT<span class="post-date">02-SEP-2020</span></div><p class="post-text">sed do eiusmod tempor incidi<br>dunt ut labore et dolore magna<br>aliqua. Ut enim ad minim veni<br>am, quis nostrud</p></div></article>
    <article class="post post--active" style="left:37px;top:144px"><div class="post-photo" role="img" aria-label="Hemp field at sunset" style="background:linear-gradient(180deg,#c9a97e,#8a8a5a 35%,#4e6b2c 60%,#314a1c)"></div><div class="post-body"><div class="post-title">CONSECTETUR ADIPIS<br>CING ELIT<span class="post-date">02-SEP-2020</span></div><p class="post-text">sed do eiusmod tempor incidi<br>dunt ut labore et dolore magna<br>aliqua. Ut enim ad minim veni<br>am, quis nostrud</p></div></article>
    <article class="post" style="left:201px;top:144px"><div class="post-photo" role="img" aria-label="Hand holding a hemp flower" style="background:linear-gradient(135deg,#6d6a4a,#8d9460 45%,#3e4a26)"></div><div class="post-body"><div class="post-title">CONSECTETUR ADIPIS<br>CING ELIT<span class="post-date">02-SEP-2020</span></div><p class="post-text">sed do eiusmod tempor incidi<br>dunt ut labore et dolore magna<br>aliqua. Ut enim ad minim veni<br>am, quis nostrud</p></div></article>
  </section>

  <footer class="footer" role="img" aria-label="Dark hemp field behind the footer">
    <div class="news-label">SUBSCRIBE OUR NEWSLETTER NOW !</div>
    <div class="news-input">Enter the Email</div>
    <div class="news-btn">SUBSCRIBE</div>
    <div class="rule"></div>
    <div class="brand">kestrelbrookhollow.com</div>
    <p class="footer-about">ut aliquip ex ea commodo consequat. Duis aute irure dolor in reprehenderit in voluptate velit esse cillum dolore eu fugiat nulla pariatur. Excepteur sint</p>
    <div class="socials"><i></i><i></i><i></i><i></i></div>
    <div class="col-title" style="left:175px;top:67px">QUICKS LINKS</div>
    <div class="links">Home<br>About Us<br>Services<br>Blog<br>Contact Us</div>
    <div class="col-title" style="left:277px;top:65px">CONTACT US</div>
    <div class="contact-row" style="top:81px"><svg width="5" height="6" viewBox="0 0 5 6"><path d="M2.5 6 C1 4 0 3 0 2 A2.5 2.5 0 0 1 5 2 C5 3 4 4 2.5 6Z" fill="#fff"/><circle cx="2.5" cy="2" r=".8" fill="#18221d"/></svg><span>Lorem ipsum dolor<br>sit amet</span></div>
    <div class="contact-row" style="top:104px"><svg width="5" height="5" viewBox="0 0 5 5"><rect width="5" height="5" rx="1" fill="#fff"/><path d="M1.3 1.2 L2 1.2 L2.3 2 L1.9 2.3 C2.2 2.9 2.4 3.1 3 3.4 L3.3 3 L4 3.3 L4 4 C2.5 4 1.2 2.8 1.3 1.2Z" fill="#18221d"/></svg><span>1 555 014 2290</span></div>
    <div class="contact-row" style="top:120px"><svg width="6" height="5" viewBox="0 0 6 5"><rect width="6" height="4.4" fill="#fff"/><path d="M0 0 L3 2.4 L6 0" fill="none" stroke="#18221d" stroke-width=".5"/></svg><span>info@kestrelbrookhollow.com</span></div>
    <div class="copyright">© Copyrights@ 2020 Kestrel Brook Hollow |&nbsp; All Rights Reserved</div>
    <div class="code">C43</div>
  </footer>

  <div class="gate-shade"></div>
  <div class="gate" role="dialog" aria-label="Age confirmation">
    <p class="gate-question">Are you over 20 years old?</p>
    <div class="gate-btn gate-yes">Yes</div>
    <div class="gate-btn gate-no">No</div>
  </div>
</div>

<!-- ============ PAGE AFTER ENTRY ============ -->
<div class="page page--open">
  <section class="hero" role="img" aria-label="Dark close-up of hemp leaves">
    <div class="brand">kestrelbrookhollow.com</div>
    <nav class="nav"><span class="active" style="left:153px">Home</span><span style="left:184px">About Us</span><span style="left:224px">Services</span><span style="left:261px">Blog</span><span style="left:289px">Contact Us</span></nav>
    <svg class="search" width="6" height="6" viewBox="0 0 6 6"><circle cx="2.4" cy="2.4" r="1.8" fill="none" stroke="#fff" stroke-width=".8"/><line x1="3.7" y1="3.7" x2="5.5" y2="5.5" stroke="#fff" stroke-width=".8"/></svg>
    <h1 class="hero-title">Pause, Play, Rewind</h1>
    <p class="hero-text">Lorem ipsum dolor sit amet, consectetur adipiscing elit, sed<br>do eiusmod tempor incididunt ut labore et dolore magna<br>aliqua.</p>
    <div class="btn">GET STARTED</div>
    <div class="rail" style="top:65px;height:11px;width:1.2px;background:#fff"></div>
    <div class="rail" style="top:81px;height:21px"></div>
    <div class="rail" style="top:105px;height:14px"></div>
    <svg class="notch" width="397" height="13" viewBox="0 0 397 13"><path d="M168 13 C180 13 182 1 199 1 C216 1 218 13 230 13 Z" fill="#fff"/><rect x="197" y="4" width="4" height="6" rx="2" fill="none" stroke="#555" stroke-width=".5"/></svg>
  </section>

  <section class="history">
    <div class="history-photo" role="img" aria-label="Hemp seedlings sprouting from soil-filled shells with green leaves"></div>
    <div class="eyebrow">LOREM IPSUM DOLOR SIT</div>
    <h2 class="heading">HISTORY ABOUT KESTREL BROOK</h2>
    <p class="history-text">Lorem ipsum dolor sit amet, consectetur adipiscing elit, sed do eiusmod tempor incididunt ut labore et dolore magna aliqua. Ut enim ad minim veniam, quis nostrud exercitation ullamco laboris nisi ut aliquip ex ea commodo consequat. Duis aute irure dolor in reprehenderit in voluptate velit esse cillum dolore eu fugiat nulla pariatur. Excepteur sint occaecat cupidatat non proident, sunt in culpa qui officia deserunt mollit anim id est laborum.</p>
    <div class="btn">GET STARTED</div>
  </section>

  <section class="services" role="img" aria-label="Dark field of hemp plants behind the services list">
    <div class="eyebrow center">LOREM IPSUM DOLOR SIT</div>
    <h2 class="heading center">OUR SERVICES</h2>
    <div class="service" style="left:34px"><svg width="16" height="16" viewBox="0 0 16 16" fill="none" stroke="#d9a420" stroke-width=".9"><path d="M2 14 C6 12 10 4 14 2"/><path d="M2 10 C6 12 10 4 14 6"/><line x1="5" y1="9" x2="7" y2="11"/><line x1="8" y1="6" x2="10" y2="8"/></svg><h3>GENETICS</h3><p>Lorem ipsum dolor sit amet,<br>consectetur adipiscing elit, sed<br>do eiusmod tempor.</p></div>
    <div class="service" style="left:117px"><svg width="16" height="16" viewBox="0 0 16 16" fill="none" stroke="#d9a420" stroke-width=".9"><rect x="5" y="1" width="10" height="8"/><line x1="7" y1="4" x2="13" y2="4"/><line x1="7" y1="6" x2="11" y2="6"/><circle cx="4" cy="10" r="2"/><path d="M1 15 C1 12 7 12 7 15"/></svg><h3>CONSULTING</h3><p>Lorem ipsum dolor sit amet,<br>consectetur adipiscing elit, sed<br>do eiusmod tempor.</p></div>
    <div class="service" style="left:200px"><svg width="16" height="16" viewBox="0 0 16 16" fill="#d9a420"><circle cx="8" cy="7" r="2"/><circle cx="3" cy="4" r="1"/><circle cx="13" cy="3" r="1"/><circle cx="14" cy="9" r="1"/><circle cx="10" cy="1.5" r=".8"/><rect x="7.5" y="9" width="1" height="6"/></svg><h3>ANCILLARY</h3><p>Lorem ipsum dolor sit amet,<br>consectetur adipiscing elit, sed<br>do eiusmod tempor.</p></div>
    <div class="service" style="left:281px"><svg width="16" height="16" viewBox="0 0 16 16" fill="none" stroke="#d9a420" stroke-width=".9"><rect x="3" y="1" width="10" height="14" rx="1"/><circle cx="7" cy="6" r="2"/><line x1="10" y1="5" x2="12" y2="5"/><line x1="5" y1="11" x2="5" y2="13"/><line x1="8" y1="10" x2="8" y2="13"/><line x1="11" y1="9" x2="11" y2="13"/></svg><h3>BIOMASS PROGRAM</h3><p>Lorem ipsum dolor sit amet,<br>consectetur adipiscing elit, sed<br>do eiusmod tempor.</p></div>
  </section>

  <section class="clients">
    <div class="eyebrow center">LOREM IPSUM DOLOR SIT</div>
    <h2 class="heading center">WHAT OUR CLIENTS SAY</h2>
    <div class="quote" style="left:37px">Lorem ipsum dolor sit amet, conse<br>ctetur adipiscing elit, sed do eiusmod tempor<br>incididunt ut labore et dolore magna aliqua.<br>Ut enim ad minim veniam, quis nostrud<br>exercitation ullamco laboris nisi ut<div class="avatar" role="img" aria-label="Client portrait"></div><div class="client-name">John Doe</div></div>
    <div class="quote" style="left:147px">Lorem ipsum dolor sit amet, conse<br>ctetur adipiscing elit, sed do eiusmod tempor<br>incididunt ut labore et dolore magna aliqua.<br>Ut enim ad minim veniam, quis nostrud<br>exercitation ullamco laboris nisi ut<div class="avatar" role="img" aria-label="Client portrait"></div><div class="client-name">John Doe</div></div>
    <div class="quote" style="left:258px">Lorem ipsum dolor sit amet, conse<br>ctetur adipiscing elit, sed do eiusmod tempor<br>incididunt ut labore et dolore magna aliqua.<br>Ut enim ad minim veniam, quis nostrud<br>exercitation ullamco laboris nisi ut<div class="avatar" role="img" aria-label="Client portrait"></div><div class="client-name">John Doe</div></div>
  </section>

  <section class="blog">
    <div class="eyebrow center">LOREM IPSUM DOLOR SIT</div>
    <h2 class="heading center">OUR LATEST BLOG</h2>
    <article class="post" style="left:37px;top:80px"><div class="post-photo" role="img" aria-label="Hemp plant in sunlight" style="background:linear-gradient(135deg,#e9e2a8,#6f8a3a 45%,#2f4a1e)"></div><div class="post-body"><div class="post-title">CONSECTETUR ADIPIS<br>CING ELIT<span class="post-date">02-SEP-2020</span></div><p class="post-text">sed do eiusmod tempor incidi<br>dunt ut labore et dolore magna<br>aliqua. Ut enim ad minim veni<br>am, quis nostrud</p></div></article>
    <article class="post" style="left:201px;top:80px"><div class="post-photo" role="img" aria-label="Researcher inspecting hemp plants" style="background:linear-gradient(135deg,#c9cfc2,#7c8f62 50%,#3d5128)"></div><div class="post-body"><div class="post-title">CONSECTETUR ADIPIS<br>CING ELIT<span class="post-date">02-SEP-2020</span></div><p class="post-text">sed do eiusmod tempor incidi<br>dunt ut labore et dolore magna<br>aliqua. Ut enim ad minim veni<br>am, quis nostrud</p></div></article>
    <article class="post post--active" style="left:37px;top:144px"><div class="post-photo" role="img" aria-label="Hemp field at sunset" style="background:linear-gradient(180deg,#c9a97e,#8a8a5a 35%,#4e6b2c 60%,#314a1c)"></div><div class="post-body"><div class="post-title">CONSECTETUR ADIPIS<br>CING ELIT<span class="post-date">02-SEP-2020</span></div><p class="post-text">sed do eiusmod tempor incidi<br>dunt ut labore et dolore magna<br>aliqua. Ut enim ad minim veni<br>am, quis nostrud</p></div></article>
    <article class="post" style="left:201px;top:144px"><div class="post-photo" role="img" aria-label="Hand holding a hemp flower" style="background:linear-gradient(135deg,#6d6a4a,#8d9460 45%,#3e4a26)"></div><div class="post-body"><div class="post-title">CONSECTETUR ADIPIS<br>CING ELIT<span class="post-date">02-SEP-2020</span></div><p class="post-text">sed do eiusmod tempor incidi<br>dunt ut labore et dolore magna<br>aliqua. Ut enim ad minim veni<br>am, quis nostrud</p></div></article>
  </section>

  <footer class="footer" role="img" aria-label="Dark hemp field behind the footer">
    <div class="news-label">SUBSCRIBE OUR NEWSLETTER NOW !</div>
    <div class="news-input">Enter the Email</div>
    <div class="news-btn">SUBSCRIBE</div>
    <div class="rule"></div>
    <div class="brand">kestrelbrookhollow.com</div>
    <p class="footer-about">ut aliquip ex ea commodo consequat. Duis aute irure dolor in reprehenderit in voluptate velit esse cillum dolore eu fugiat nulla pariatur. Excepteur sint</p>
    <div class="socials"><i></i><i></i><i></i><i></i></div>
    <div class="col-title" style="left:175px;top:67px">QUICKS LINKS</div>
    <div class="links">Home<br>About Us<br>Services<br>Blog<br>Contact Us</div>
    <div class="col-title" style="left:277px;top:65px">CONTACT US</div>
    <div class="contact-row" style="top:81px"><svg width="5" height="6" viewBox="0 0 5 6"><path d="M2.5 6 C1 4 0 3 0 2 A2.5 2.5 0 0 1 5 2 C5 3 4 4 2.5 6Z" fill="#fff"/><circle cx="2.5" cy="2" r=".8" fill="#18221d"/></svg><span>Lorem ipsum dolor<br>sit amet</span></div>
    <div class="contact-row" style="top:104px"><svg width="5" height="5" viewBox="0 0 5 5"><rect width="5" height="5" rx="1" fill="#fff"/><path d="M1.3 1.2 L2 1.2 L2.3 2 L1.9 2.3 C2.2 2.9 2.4 3.1 3 3.4 L3.3 3 L4 3.3 L4 4 C2.5 4 1.2 2.8 1.3 1.2Z" fill="#18221d"/></svg><span>1 555 014 2290</span></div>
    <div class="contact-row" style="top:120px"><svg width="6" height="5" viewBox="0 0 6 5"><rect width="6" height="4.4" fill="#fff"/><path d="M0 0 L3 2.4 L6 0" fill="none" stroke="#18221d" stroke-width=".5"/></svg><span>info@kestrelbrookhollow.com</span></div>
    <div class="copyright">© Copyrights@ 2020 Kestrel Brook Hollow |&nbsp; All Rights Reserved</div>
    <div class="code">C43</div>
  </footer>
</div>

</body>
</html>
```